UI design for an Zyn(Halvo) photo editing app

This design contest is to design the UI/screenshots of an Zyn(Halvo) app named "Kestrel Pix". Some minor design details are left out at this point as the mockup is still in progress. The icon of this app will be designed separately. The winner of this job will be selected to work on a long term basis as an Dorvo version and several updates will have to be designed as well as the Quillex version. Please take
this as a long term opportunity.
The photo app is called "Kestrel Pix". The design need to dynamic, different that stands out WITH a serious and polished look.
All the mockups and sample screenshots are attached for ease. Please thoroughly review them.
This app has the following screens:
1. Welcome screen(just a simple background will do now as icon will be put later).
2. Main Screen (or LightBox)
The background of this screen can be the same as the background of the welcome screen. It can be a wooden background OR a background of your
choice that fits and blends in the buttons and fonts/colors.
The main screen has this bars/buttons/options that has separate screens:
On top, menu bar:
has these buttons
settings on the left(icon)
in the middle, 3 buttons (please check lightbox mockup and lightbox sample pics)
on the right, share icon(check share screen sample)
Our share options:
"Share" button screenshot:
Our share options:
Save
Email
Copy
Moodlefy
Chatterbay
Zorbly
Quorra
in the middle, just background where the pictures would appear later after importing
or saving
at the bottom bar:
3 buttons:
Camera Roll(on the left)
Camera Button(middle)
Advanced Button(on the right)
2 versions of this screenshot need to be designed.
1. regular version with all the options
2. regular version plus the "steam effect" button showing up on top of the "Advanced" button(mockup with red lines)
3 separate screenshots need to be designed for the options"
settings screenshot(please check sample):
Gift Kestrel Pix to a friend
Rate/review in the Tundle Hub
(space in between...so they are grouped)
Geotagiing(on/off)
Captured photos get location-specific information(these lines in smaller fonts)
Launch in Capture Mode(on/off)
Kestrel Pix is automatically lauched in camera mode
Autosave to Camera Roll(on/off)
Captured photos are directly saved to camera roll
Reset All Tutorials
Tap to reset all the tutorials
In the "Steam Effect" screen, please check the mockup
Top Bar: lightbox button(to go back), heading and Done button
Middle: Steam background(provided)
Bottom bar:
refresh button
droplets(when clicked on/off options show up on top, please check mockup)
finger size(when clicked 3 options show up)
steam density(when clicked 3 options show up)
Please use the buttons for the droplets, finger size and steam density from the steam effects button image provided)
(and also the background of this screenshot(in the middle) would be a steam screen which is provided. Please use the
steam background provided and you need to use the background in the middle, just omit the top and the bottom bar from the image)
Now back to the main(lightbox screen):
When Clicked on the "Camera" in the middle of the bottom bar, the capture mode screen shows up.
Please refer to the mockup first
There you will see the cancel button on the left
camera button in the middle
a small settings button on the right
and a filters button on the right
and the filters bar on the top
ours need to like this
please refer to capture mode sample 1
please refer to capture mode sample 2
please refer to capture mode sample 3
normal
Grid
timer(5/15/30 secs)
Edit Screen(check sample)
Edit options
Adjust:(displayed on a bar)
1. Left
2. Right
3. Horizontal
4. Vertical
5. Straightening
Crop:
None
Original
Golden
Freeform
Square
3:2
4:3
4:6
5:7
8:10
16:9
Filters:(please note that this filter icon and the filter icon in the "capture mode" screenshot need to same)
(the filters are displayed on a bar, please check sample)
There is a sample picture that you need to put in the picture of the filters. It would be same picture in
every filter at this point.
00.None
0.Calibrate
1. aurora
2. drizzle
3. icicle
4. blizzard
5. calm
6. dew
7. knot
8. dry
9. eye
10. flurry
11. fog
12. frost
13. hail
14. haze
15. heat
16. humid
17. overcast
18. polar
19. thermal
20. trace
Editing options on top:(check sample)
Brightness
Contrast
Saturation
Textures:(dispalyed on a bar, check sample)
1.None
2.Bark
3.Grunge1
4.Grunge2
5.grunge3
6.Grunge4
7.Paper
8.Cardboard
9.Wood
10.Bokeh
11.Bricks
12.Metal
13.Asphalt
14.Pavement1
15.Pavement2
16.Paint1
17.Paint2
18.Rust
19.Towel
20.Stone1
21.Stone2
22.Wall
23.Urban1
24.Urban2
25.Urban3
26.Watercolor
Tilt-shift/Vignette:(check sample)
Borders:(check samples, at this point, we are working on them, you just need to make a bar that displays them)
1.None
2.
3.
4.
5.
6.
7.
8.
9.
10.
11.
12.
13.
14.
15.
16.
This is our primary design mockup. Upon selecting the final version, we will be working on some more and minor details(as
we are also working with the coders).
And there is a folder callled "app sample". Please take a look at it and think how our app can be different and stand out.
Thanks and feel free to contact me anytime if you have any questions. Looking forward to hearing from you and building a long term
relationship.
All camera app users who likes to edit their photos with cool tools.
Building

```html
<!DOCTYPE html>
<html lang="en">
<head>
<meta charset="utf-8">
<title>Kestrel Pix – App Screens</title>
<link rel="stylesheet" href="https://fonts.googleapis.com/css2?family=Open+Sans:wght@400;600;700&display=swap">
<style>
:root{
  --page:#f2f2f2;
  --ink:#111111;
  --red:#b3121c;
  --red-dark:#7c0a10;
  --red-bright:#d8262f;
  --screen-black:#0d0d0d;
  --row-light:#f4f4f4;
  --row-dark:#3a3a3a;
  --line:#cfcfcf;
  --muted:#8a8a8a;
  --wheel:#dcdcdc;
  --photo-warm:#8a7a6e;
  --photo-cool:#55606a;
}
*{box-sizing:border-box;margin:0;padding:0}
html,body{width:1200px;height:755px;overflow:hidden;background:var(--page);font-family:"Open Sans",Arial,sans-serif;color:var(--ink)}
.canvas{position:relative;width:1200px;height:755px}
.app-title{position:absolute;top:38px;left:0;width:100%;text-align:center;font-size:50px;font-weight:400;letter-spacing:-1px}
.screen{position:absolute;background:var(--screen-black);overflow:hidden;box-shadow:0 6px 18px rgba(0,0,0,.18)}
.portrait{width:230px;height:345px;top:215px}
/* edit screen */
.edit-screen{left:36px;top:340px;width:330px;height:220px;background:#1a1a1a}
.status-bar{position:absolute;top:0;left:0;right:0;height:14px;background:#000;color:#fff;font-size:8px;font-weight:700;padding:1px 6px}
.edit-photo{position:absolute;top:14px;left:0;width:150px;bottom:0;background:linear-gradient(135deg,#6a7a70,#c9c2b3 55%,#4e5a5a)}
.thumb-strip{position:absolute;top:14px;left:150px;width:34px;bottom:0;background:#222;display:flex;flex-direction:column;gap:3px;padding:4px}
.thumb{flex:1;background:linear-gradient(135deg,#5b7082,#9cb3c2);border:1px solid #eee}
.edit-slider{position:absolute;top:26px;left:202px;width:20px;bottom:14px}
.edit-slider .track{position:absolute;left:8px;top:0;bottom:0;width:4px;background:#555;border-radius:2px}
.edit-slider .fill{position:absolute;left:8px;top:0;height:60%;width:4px;background:var(--red-bright);border-radius:2px}
.edit-slider .knob{position:absolute;left:2px;top:56%;width:16px;height:16px;border-radius:50%;background:radial-gradient(circle at 40% 35%,#fff,#aaa)}
.adjust-tabs{position:absolute;top:14px;right:0;width:90px;bottom:0;display:flex;flex-direction:column}
.adjust-tab{flex:1;display:flex;align-items:center;justify-content:center;background:#d9d9d9;color:#333;font-size:11px;font-weight:700;border-bottom:1px solid #aaa}
.adjust-tab.is-active{background:#2a2a2a;color:#fff}
/* capture screen */
.capture-screen{left:402px}
.capture-photo{position:absolute;inset:0 0 40px 0;background:linear-gradient(160deg,#b49d8d,#6e5d52 50%,#2d2a2a)}
.timer-dial{position:absolute;left:15px;top:45px}
.zoom-row{position:absolute;left:10px;right:10px;bottom:52px;display:flex;align-items:center;gap:6px;color:#fff;font-size:9px;font-weight:700}
.zoom-track{flex:1;height:5px;border-radius:3px;background:linear-gradient(90deg,#eee 30%,var(--red-bright) 30%)}
.bottom-bar{position:absolute;left:0;right:0;bottom:0;height:40px;background:linear-gradient(var(--red-bright),var(--red-dark));display:flex;align-items:center;justify-content:space-around;padding:0 6px}
.small-btn{background:linear-gradient(#f5f5f5,#bbb);color:var(--red-dark);font-size:8px;font-weight:700;padding:3px 7px;border-radius:4px}
/* settings */
.settings-screen{left:668px}
.nav-bar{height:32px;background:linear-gradient(var(--red-bright),var(--red-dark));display:flex;align-items:center;justify-content:space-between;padding:0 7px;color:#fff}
.nav-title{font-size:13px;font-weight:700}
.section-label{color:#fff;font-size:8px;text-align:center;margin:6px 0 3px}
.segmented{display:flex;margin:0 14px;border-radius:3px;overflow:hidden}
.segment{flex:1;text-align:center;font-size:8px;font-weight:700;padding:4px 0;background:linear-gradient(#e9eef3,#b8c2cc);color:var(--red-dark)}
.segment.is-active{background:linear-gradient(#fff,#ddd)}
.settings-list{margin:5px 14px 0;display:flex;flex-direction:column;gap:3px}
.setting-row{height:21px;display:flex;align-items:center;gap:8px;padding:0 7px;background:var(--row-light);font-size:6.5px;font-weight:700;color:#333}
.setting-row.is-dark{background:var(--row-dark);color:#fff;margin-top:-3px;border-top:1px solid #555}
.setting-row .label{flex:1;line-height:1.1}
.setting-row .note{display:block;font-size:4.5px;font-weight:400;color:var(--muted)}
.row-icon{width:9px;height:7px;background:#555;border-radius:1px}
.is-dark .row-icon{background:#ddd}
.check{width:9px;height:9px;border:1px solid #999;background:#ddd;border-radius:1px;position:relative}
.check.on{background:var(--red-bright);border-color:var(--red-dark)}
.check.on::after{content:"";position:absolute;left:2px;top:0;width:3px;height:5px;border:solid #fff;border-width:0 1.5px 1.5px 0;transform:rotate(45deg)}
.reset-btn{margin:18px auto 0;width:120px;border-radius:12px;background:linear-gradient(#fafafa,#c9c9c9);text-align:center;padding:3px 0;font-size:6px;font-weight:700;color:#555}
.reset-btn span{display:block;font-size:4.5px;font-weight:400;color:var(--red)}
/* share */
.share-screen{left:934px}
.top-bar{height:34px;background:linear-gradient(var(--red-bright),var(--red-dark));display:flex;align-items:center;justify-content:space-between;padding:0 8px}
.share-photo{position:absolute;top:50px;left:12px;right:12px;height:200px;background:linear-gradient(140deg,#6f6862,#3b3a3a 60%,#2a2a2a)}
.share-wheel{position:absolute;left:29px;top:72px}
.square-btn{width:28px;height:20px;background:var(--red-dark);border:1px solid #5a0408;border-radius:2px}
</style>
</head>
<body>
<main class="canvas">
  <h1 class="app-title">Kestrel Pix</h1>

  <!-- Edit screen -->
  <section class="screen edit-screen">
    <div class="status-bar">▮▮▮▮ 3G</div>
    <div class="edit-photo" role="img" aria-label="Photo being edited"></div>
    <div class="thumb-strip">
      <div class="thumb" role="img" aria-label="Filter preview"></div>
      <div class="thumb" role="img" aria-label="Filter preview"></div>
      <div class="thumb" role="img" aria-label="Filter preview"></div>
      <div class="thumb" role="img" aria-label="Filter preview"></div>
      <div class="thumb" role="img" aria-label="Filter preview"></div>
      <div class="thumb" role="img" aria-label="Filter preview"></div>
    </div>
    <div class="edit-slider"><div class="track"></div><div class="fill"></div><div class="knob"></div></div>
    <div class="adjust-tabs">
      <div class="adjust-tab is-active">Brightness</div>
      <div class="adjust-tab">Contrast</div>
      <div class="adjust-tab">Saturation</div>
    </div>
  </section>

  <!-- Capture screen -->
  <section class="screen portrait capture-screen">
    <div class="capture-photo" role="img" aria-label="Live camera view of a desk"></div>
    <svg class="timer-dial" width="200" height="200" viewBox="-100 -100 200 200">
      <circle r="68" fill="none" stroke="#d23a44" stroke-width="34" stroke-dasharray="10 3"/>
      <circle r="68" fill="none" stroke="#6a0a10" stroke-width="34" stroke-dasharray="0 290 140 0" opacity=".75"/>
      <circle r="46" fill="#111"/>
      <circle r="40" fill="#1e1e1e" stroke="#444"/>
      <text y="6" text-anchor="middle" fill="#fff" font-size="30" font-weight="700">5</text>
      <text y="22" text-anchor="middle" fill="#fff" font-size="9">SEC.</text>
      <text x="-30" y="-86" fill="#f3c4c7" font-size="13" font-weight="700" transform="rotate(10)">Set Timer</text>
      <text y="98" text-anchor="middle" fill="#fff" font-size="11" font-weight="700">Timer Active</text>
    </svg>
    <div class="zoom-row"><span>1.5x</span><div class="zoom-track"></div></div>
    <div class="bottom-bar">
      <span class="small-btn">Cancel</span>
      <svg width="26" height="22" viewBox="0 0 26 22"><rect x="1" y="5" width="24" height="16" rx="3" fill="none" stroke="#fff" stroke-width="2"/><rect x="8" y="1" width="10" height="5" rx="1" fill="#fff"/><circle cx="13" cy="13" r="5" fill="none" stroke="#fff" stroke-width="2"/></svg>
      <svg width="16" height="16" viewBox="0 0 16 16"><circle cx="8" cy="8" r="6" fill="none" stroke="#fff" stroke-width="2" stroke-dasharray="6 3"/></svg>
      <svg width="16" height="16" viewBox="0 0 16 16"><circle cx="8" cy="8" r="5" fill="none" stroke="#fff" stroke-width="3" stroke-dasharray="2 2"/><circle cx="8" cy="8" r="2" fill="#fff"/></svg>
    </div>
  </section>

  <!-- Settings screen -->
  <section class="screen portrait settings-screen">
    <header class="nav-bar">
      <span class="small-btn">Back</span>
      <span class="nav-title">Settings</span>
      <span class="small-btn">Save</span>
    </header>
    <p class="section-label">Image Quality</p>
    <div class="segmented">
      <span class="segment">Low</span><span class="segment is-active">Medium</span><span class="segment">High</span>
    </div>
    <div class="settings-list">
      <div class="setting-row"><span class="row-icon"></span><span class="label">GeoTagging<span class="note">Captured photos get location specific information</span></span><span class="check"></span></div>
      <div class="setting-row"><span class="row-icon"></span><span class="label">Camera Roll</span><span class="check on"></span></div>
      <div class="setting-row"><span class="row-icon"></span><span class="label">Capture Mode</span><span class="check on"></span></div>
      <div class="setting-row"><span class="row-icon"></span><span class="label">Share Settings</span><span>+</span></div>
      <div class="setting-row is-dark"><span class="row-icon"></span><span class="label">Moodlefy</span><span class="check on"></span></div>
      <div class="setting-row is-dark"><span class="row-icon"></span><span class="label">Quorra</span><span class="check"></span></div>
      <div class="setting-row is-dark"><span class="row-icon"></span><span class="label">Zorbly</span><span class="check on"></span></div>
      <div class="setting-row is-dark"><span class="row-icon"></span><span class="label">Chatterbay</span><span class="check"></span></div>
      <div class="setting-row"><span class="row-icon"></span><span class="label">Rate/Review Kestrel Pix</span><span>&gt;</span></div>
    </div>
    <div class="reset-btn">RESET ALL TUTORIALS<span>Tap to reset all the tutorials</span></div>
  </section>

  <!-- Share screen -->
  <section class="screen portrait share-screen">
    <header class="top-bar">
      <svg width="14" height="14" viewBox="0 0 16 16"><circle cx="8" cy="8" r="5" fill="none" stroke="#fff" stroke-width="3" stroke-dasharray="2 2"/><circle cx="8" cy="8" r="2" fill="#fff"/></svg>
      <svg width="30" height="14" viewBox="0 0 30 14"><rect x="1" y="2" width="28" height="10" rx="5" fill="#555"/><circle cx="22" cy="7" r="5" fill="#eee"/></svg>
      <svg width="16" height="16" viewBox="0 0 16 16"><circle cx="3" cy="8" r="2.5" fill="#fff"/><circle cx="13" cy="3" r="2.5" fill="#fff"/><circle cx="13" cy="13" r="2.5" fill="#fff"/><path d="M3 8 13 3M3 8 13 13" stroke="#fff" stroke-width="1.5"/></svg>
    </header>
    <div class="share-photo" role="img" aria-label="Imported photo of a camera"></div>
    <svg class="share-wheel" width="172" height="172" viewBox="-86 -86 172 172">
      <circle r="82" fill="var(--wheel)" stroke="#fff" stroke-width="3"/>
      <g stroke="#aaa" stroke-width="1">
        <line x1="0" y1="-22" x2="0" y2="-80"/><line x1="0" y1="22" x2="0" y2="80"/>
        <line x1="-22" y1="0" x2="-80" y2="0"/><line x1="22" y1="0" x2="80" y2="0"/>
        <line x1="15.6" y1="-15.6" x2="56.6" y2="-56.6"/><line x1="-15.6" y1="-15.6" x2="-56.6" y2="-56.6"/>
        <line x1="15.6" y1="15.6" x2="56.6" y2="56.6"/><line x1="-15.6" y1="15.6" x2="-56.6" y2="56.6"/>
      </g>
      <g font-size="7" font-weight="700" fill="#333" text-anchor="middle">
        <text x="-22" y="-46">Chatterbay</text><text x="22" y="-46">Quorra</text>
        <text x="52" y="-18">Close</text><text x="52" y="22">Zorbly</text>
        <text x="22" y="52">Email</text><text x="-22" y="52">Copy</text>
        <text x="-52" y="22">Save</text><text x="-52" y="-18">Moodlefy</text>
      </g>
      <circle r="22" fill="#000"/>
      <text y="3" text-anchor="middle" fill="#ccc" font-size="8">Share</text>
    </svg>
    <div class="bottom-bar">
      <span class="square-btn"></span>
      <svg width="26" height="22" viewBox="0 0 26 22"><rect x="1" y="5" width="24" height="16" rx="3" fill="none" stroke="#fff" stroke-width="2"/><rect x="8" y="1" width="10" height="5" rx="1" fill="#fff"/><circle cx="13" cy="13" r="5" fill="none" stroke="#fff" stroke-width="2"/></svg>
      <span class="square-btn"></span>
    </div>
  </section>
</main>
</body>
</html>
```